BLS Business Card 2018

Larkmere Chiropractic. We have two locations that we want to advertise on the same card. Brightvale OrthoCore campus address: 3815 Pellham Dr., Suite 240, Flowood, MS 39417. Madison address: 246 Willowmere Dr., Building D., Madison, MS 39284. website: www.drlarkmere-example.com. o:(601)555-0147 f:(601)555-0183

Target Market(s)

Health care decision makers: primary care doctors and mothers

Contact Information for Business Card

I have no idea; up for any suggestions and I'd do much better picking from examples versus describing what I'm looking for. We are in a very high end location and would like the cards to look really sharp.

Requirements
Must have
• My name, Martin R Belvane, D.C.

```html
<!DOCTYPE html>
<html lang="en">
<head>
<meta charset="utf-8">
<title>Larkmere Chiropractic – Business Card</title>
<link href="https://fonts.googleapis.com/css2?family=Merriweather:wght@400;700&display=swap" rel="stylesheet">
<style>
  :root {
    --backdrop: #3b3c3f;
    --card: #1f2023;
    --card-edge: #17181a;
    --band: #0e5e85;
    --accent: #1c86d6;
    --white: #ffffff;
    --muted: #c9ccd1;
    --emboss: #2d2e32;
  }
  * { margin: 0; padding: 0; box-sizing: border-box; }
  html, body { width: 799px; height: 1200px; overflow: hidden; }
  body {
    background: var(--backdrop);
    font-family: "Merriweather", Georgia, serif;
    color: var(--white);
    position: relative;
  }
  .card {
    position: absolute;
    left: 60px;
    width: 680px;
    height: 400px;
    background: var(--card);
    border-radius: 26px;
    overflow: hidden;
    box-shadow: 0 14px 30px rgba(0,0,0,.45);
  }
  .card--front { top: 90px; }
  .card--back { top: 710px; }

  /* Front */
  .front-brand {
    position: absolute; left: 290px; top: 62px;
    color: var(--emboss); font-weight: 700; text-transform: uppercase; line-height: 1;
  }
  .front-brand .line1 { display: block; font-size: 50px; letter-spacing: 1px; }
  .front-brand .line2 { display: block; font-size: 36px; letter-spacing: 2px; margin-top: 4px; padding-left: 10px; }
  .band {
    position: absolute; left: 0; top: 205px; width: 100%; height: 95px;
    background: var(--band);
  }
  .campus-pill {
    position: absolute; left: 235px; top: 180px; width: 210px; height: 46px;
    border: 2px solid var(--white); border-radius: 23px; background: var(--card);
    display: flex; align-items: center; justify-content: center;
    font-size: 15px; font-weight: 700;
  }
  .address {
    position: absolute; top: 238px; display: flex; gap: 8px;
    font-size: 14px; line-height: 1.35;
  }
  .address--flowood { left: 50px; }
  .address--madison { left: 378px; }
  .address svg { flex: none; margin-top: 2px; }
  .band-divider {
    position: absolute; left: 346px; top: 240px; width: 1px; height: 42px;
    background: rgba(255,255,255,.5);
  }
  .front-web {
    position: absolute; left: 0; top: 330px; width: 100%;
    display: flex; align-items: center; justify-content: center; gap: 18px;
    font-size: 15px;
  }
  .front-web .rule { width: 60px; height: 2px; background: var(--white); }

  /* Back */
  .back-brand {
    position: absolute; left: 48px; top: 48px;
    font-weight: 700; text-transform: uppercase; line-height: 1; color: var(--white);
  }
  .back-brand .line1 { display: block; font-size: 44px; letter-spacing: 1px; }
  .back-brand .line2 { display: block; font-size: 32px; letter-spacing: 2px; margin-top: 4px; padding-left: 6px; }
  .person-name {
    position: absolute; left: 50px; top: 168px;
    font-size: 22px; font-weight: 700; color: var(--accent);
  }
  .person-role {
    position: absolute; left: 50px; top: 200px;
    font-size: 12px; color: var(--muted);
  }
  .contact-list {
    position: absolute; left: 50px; top: 234px; list-style: none;
    font-size: 14px; line-height: 24px;
  }
  .contact-list li { display: flex; align-items: center; gap: 10px; }
  .figure-art {
    position: absolute; left: 420px; top: 70px; width: 240px; height: 330px;
    border-radius: 120px 120px 0 0;
    background: radial-gradient(ellipse at 50% 40%, rgba(28,134,214,.35), rgba(28,134,214,.08) 70%, transparent);
  }
</style>
</head>
<body>

<section class="card card--front" aria-label="Card front">
  <div class="front-brand"><span class="line1">Larkmere</span><span class="line2">Chiropractic</span></div>
  <div class="band"></div>
  <div class="campus-pill">OrthoCore Campus</div>
  <div class="address address--flowood">
    <svg width="12" height="16" viewBox="0 0 12 16"><path d="M6 0a6 6 0 0 0-6 6c0 4.5 6 10 6 10s6-5.5 6-10a6 6 0 0 0-6-6zm0 8.5A2.5 2.5 0 1 1 6 3.5a2.5 2.5 0 0 1 0 5z" fill="#fff"/></svg>
    <p>3815 Pellham Dr., Suite 240,<br>Flowood, MS 39417</p>
  </div>
  <div class="band-divider"></div>
  <div class="address address--madison">
    <svg width="12" height="16" viewBox="0 0 12 16"><path d="M6 0a6 6 0 0 0-6 6c0 4.5 6 10 6 10s6-5.5 6-10a6 6 0 0 0-6-6zm0 8.5A2.5 2.5 0 1 1 6 3.5a2.5 2.5 0 0 1 0 5z" fill="#fff"/></svg>
    <p>246 Willowmere Dr., Building D.,<br>Madison, MS 39284</p>
  </div>
  <div class="front-web"><span class="rule"></span><span>www.drlarkmere-example.com</span><span class="rule"></span></div>
</section>

<section class="card card--back" aria-label="Card back">
  <div class="back-brand"><span class="line1">Larkmere</span><span class="line2">Chiropractic</span></div>
  <div class="person-name">Martin R Belvane, D.C.</div>
  <div class="person-role">Managing Director</div>
  <ul class="contact-list">
    <li><svg width="12" height="12" viewBox="0 0 12 12"><path d="M2 0h3l1 3-2 1.5a7 7 0 0 0 3.5 3.5L9 6l3 1v3a2 2 0 0 1-2 2A10 10 0 0 1 0 2a2 2 0 0 1 2-2z" fill="#1c86d6"/></svg>(601)555-0147</li>
    <li><svg width="12" height="12" viewBox="0 0 12 12"><rect x="3" y="0" width="6" height="4" fill="#1c86d6"/><rect x="0" y="4" width="12" height="5" rx="1" fill="#1c86d6"/><rect x="3" y="8" width="6" height="4" fill="#1c86d6"/></svg>(601)555-0183</li>
    <li><svg width="12" height="12" viewBox="0 0 12 12"><rect x="0" y="2" width="12" height="8" fill="#1c86d6"/><path d="M0 2l6 5 6-5" stroke="#1f2023" stroke-width="1.2" fill="none"/></svg>m.r.belvane@drlarkmere-example.com</li>
    <li><svg width="12" height="12" viewBox="0 0 12 12"><circle cx="6" cy="6" r="5.5" fill="#1c86d6"/><path d="M0.5 6h11M6 0.5c-3 3-3 8 0 11M6 0.5c3 3 3 8 0 11" stroke="#1f2023" stroke-width="1" fill="none"/></svg>www.drlarkmere-example.com</li>
  </ul>
  <div class="figure-art" role="img" aria-label="Blue line drawing of a human torso and raised arm"></div>
</section>

</body>
</html>
```